Brivolt Technologies business card design

We need a business card designed with our new logo. it would be great if the card could communicate it is a technology based company.

Target Market(s)

system integrators

Industry/Entity Type

technology, IOT

Contact Information for Business Card

Name, designation, Address, telephone number, email address

Requirements
Must have
• logo and company name
Nice to have
• something to do with technology

```html
<!DOCTYPE html>
<html lang="en">
<head>
<meta charset="utf-8">
<title>Brivolt Technologies — Business Card</title>
<link rel="stylesheet" href="https://fonts.googleapis.com/css2?family=Montserrat:wght@400;500;700&display=swap">
<style>
  :root {
    --orange: #f4931f;
    --orange-deep: #e57e05;
    --charcoal: #3d3c3d;
    --paper: #ffffff;
  }
  html, body {
    margin: 0;
    padding: 0;
    width: 971px;
    height: 1200px;
    overflow: hidden;
    background: var(--paper);
  }
  .sheet {
    display: block;
    width: 971px;
    height: 1200px;
  }
  .fill-orange { fill: var(--orange); }
  .fill-orange-deep { fill: var(--orange-deep); }
  .fill-charcoal { fill: var(--charcoal); }
  .person-name {
    font-family: "Montserrat", sans-serif;
    font-weight: 700;
    font-size: 40px;
    fill: var(--charcoal);
  }
  .person-role {
    font-family: "Montserrat", sans-serif;
    font-weight: 500;
    font-size: 26px;
    letter-spacing: 1px;
    fill: var(--orange);
  }
  .brand-word {
    font-family: "Montserrat", sans-serif;
    font-weight: 700;
    fill: var(--charcoal);
  }
  .contact-text {
    font-family: "Montserrat", sans-serif;
    font-weight: 400;
    font-size: 19px;
    fill: var(--paper);
  }
  .icon-ring {
    fill: none;
    stroke: var(--paper);
    stroke-width: 3;
  }
  .icon-glyph { fill: var(--paper); }
</style>
</head>
<body>
<svg class="sheet" viewBox="0 0 1051 1300" xmlns="http://www.w3.org/2000/svg">

  <!-- Front side -->
  <g class="card-front">
    <rect class="fill-charcoal" x="0" y="340" width="500" height="117"/>
    <polygon class="fill-orange-deep" points="213,457 362,457 287,532"/>
    <polygon class="fill-orange" points="653,170 1051,170 1051,532 287,532"/>

    <g class="brand-lockup">
      <rect class="fill-orange" x="718" y="60" width="54" height="54"/>
      <text class="brand-word" x="795" y="97" font-size="46" textLength="232" lengthAdjust="spacingAndGlyphs">BRIVOLT</text>
      <text class="brand-word" x="796" y="119" font-size="17" textLength="231" lengthAdjust="spacing">TECHNOLOGIES</text>
    </g>

    <g class="identity">
      <text class="person-name" x="68" y="168">YOUR NAME</text>
      <text class="person-role" x="68" y="205">Designation</text>
      <rect class="fill-charcoal" x="117" y="230" width="244" height="3"/>
      <rect class="fill-orange" x="65" y="229" width="52" height="6"/>
    </g>

    <g class="contact-list">
      <g class="contact-address">
        <circle class="icon-ring" cx="645" cy="258" r="22"/>
        <path class="icon-glyph" d="M645 246c-5.5 0-9 4-9 9 0 6 9 15 9 15s9-9 9-15c0-5-3.5-9-9-9zm0 12.5a3.5 3.5 0 1 1 0-7 3.5 3.5 0 0 1 0 7z"/>
        <text class="contact-text" x="684" y="260">Lorem ipsum dolor sit amet,</text>
        <text class="contact-text" x="684" y="284">consectetur adipiscing elit</text>
      </g>
      <g class="contact-phone">
        <circle class="icon-ring" cx="549" cy="359" r="22"/>
        <path class="icon-glyph" d="M541 350c1-1 3-1 4 0l2 3c.6 1 .3 2-.5 2.7l-1.3 1c1 2.2 2.8 4 5 5l1-1.3c.7-.8 1.8-1 2.7-.5l3 2c1 1 1 3 0 4l-1.5 1.5c-1.5 1.5-4 1.5-7-.3-4-2.5-7.5-6-10-10-1.8-3-1.8-5.5-.3-7z"/>
        <text class="contact-text" x="595" y="366">+0123456789</text>
      </g>
      <g class="contact-email">
        <circle class="icon-ring" cx="466" cy="443" r="22"/>
        <path class="icon-glyph" d="M456 436h20v14h-20z"/>
        <path d="M456 436l10 8 10-8M456 450l7-6M476 450l-7-6" fill="none" stroke="var(--orange)" stroke-width="1.6"/>
        <text class="contact-text" x="510" y="449">abc@mail.com</text>
      </g>
    </g>
  </g>

  <!-- Back side -->
  <g class="card-back">
    <rect class="fill-charcoal" x="150" y="1056" width="762" height="75"/>
    <polygon class="fill-orange-deep" points="226,1131 313,1131 270,1174"/>
    <polygon class="fill-orange-deep" points="750,1131 836,1131 792,1174"/>
    <polygon class="fill-orange" points="0,908 266,1174 0,1174"/>
    <polygon class="fill-orange" points="1051,918 792,1174 1051,1174"/>

    <g class="brand-lockup brand-lockup--large">
      <rect class="fill-orange" x="288" y="826" width="96" height="96"/>
      <text class="brand-word" x="426" y="897" font-size="84" textLength="388" lengthAdjust="spacingAndGlyphs">BRIVOLT</text>
      <text class="brand-word" x="428" y="939" font-size="30" textLength="385" lengthAdjust="spacing">TECHNOLOGIES</text>
    </g>
  </g>
</svg>
</body>
</html>
```